Printed Circuit Board Company Web Site Design - Please see new file 82012 web design

We are a printed circuit board manufacturer. Need a company professional web site to allow our potential customers to know more about our background, capability and our products. The web site will contain three languages, which are Chinese, English and Japanese. Our audience are mainly electronic companies that procure printed circuit boards. I have a word document that have all the required text in all three languages. The final design should communicate the impression that we embrace quality, trustworthiness and long term partnership business principles.
We should have sections that allow us to post pictures of our facilities.
I have added the three files in three different languages.
Some of the information is below:
Background
RDV Harbourline Limited (RDV) was set up in Hong Kong in 2007 by two Hong Kong entrepreneurs, Mr. Tak Wong and Mr. Lok Fai. We acquired the single sided printed circuit board factory located in Dongguan City, Guangdong Province, China, from Tovand Corporation of the U.S. in 2007. In addition to RDV, Mr. Wong and Mr. Fai also own Halberd Technology Company Limited, a semiconductor company based in Hong Kong since 1997 with a total investment of over US$100 million. Halberd is engaged in the manufacturing of flexible substrates and MEMS assembly business.
RDV has been awarded TS 16949 and ISO14000 certificates since 2009 and 2004 respectively.
Business Principles
RDV Harbourline Limited strives to be a professional top notched printed circuit board supplier. We embrace four “EXCELLENCE” principles, namely, excellence in quality, excellence in prices, excellence in services and excellence in on time delivery.
We approach each customer with a long-term partnership view that delivers the lowest ownership costs and highest total values to our customers. We customize quotations and solutions in order to allow our customers to win more businesses. We believe by thinking from our customers’ points of view we will be able to create a WIN-WIN relationship.
Customers
Due to our excellent quality, services and production systems, RDV Harbourline Limited manage to service a number of large Japanese and US customers, which include:
Technical capability overview
Below is an overview of our current capability:
Target Market(s)
Electronic companies buyers
Industry/Entity Type
Business
Requirements
Must have
- Capability description
Should not have
- no cartoon

```html
<!DOCTYPE html>
<html lang="en">
<head>
<meta charset="utf-8">
<title>RDV Harbourline Limited</title>
<link href="https://fonts.googleapis.com/css2?family=Cinzel:wght@400&family=Gelasio&family=Dosis:wght@600&family=Oswald:wght@300;400&family=Alfa+Slab+One&family=Arimo:wght@400;700&display=swap" rel="stylesheet">
<style>
:root{
  --teal:#0d7a66;
  --teal-dark:#06604f;
  --teal-light:#128a74;
  --orange:#f7941d;
  --orange-light:#ffa92e;
  --text:#444;
  --line:#bfbfbf;
  --field:#eeeeee;
}
*{margin:0;padding:0;box-sizing:border-box}
html,body{width:1200px;height:1173px;overflow:hidden;background:#fff}
body{position:relative;font-family:'Arimo',Arial,sans-serif;color:var(--text)}
.abs{position:absolute}
.top-strip{left:0;top:0;width:1200px;height:7px;background:var(--teal)}
.brand{left:108px;top:24px;width:190px;font-family:'Arimo',sans-serif;font-weight:700;font-size:19px;line-height:24px;color:var(--teal);display:flex;align-items:center;gap:8px}
.brand-mark{width:14px;height:14px;background:var(--teal);flex:none}
.phone{left:966px;top:68px;display:flex;align-items:center;gap:6px;font-size:13px;color:#222}
.nav{left:99px;top:99px;width:1002px;height:35px;background:linear-gradient(#138a73,#0a6a58);border-radius:4px 4px 0 0}
.nav a{font-family:'Cinzel',serif;color:#fff;text-decoration:none;font-size:15px;letter-spacing:.5px;position:absolute;top:8px}
.login{position:absolute;right:0;top:0;width:88px;height:35px;background:var(--orange);border-radius:0 4px 0 0;display:flex;align-items:center;justify-content:center;gap:8px;color:#fff;font-weight:700;font-size:15px}
.banner{left:99px;top:134px;width:1002px;height:304px;border:1px solid #9cc7bd;overflow:hidden;background:linear-gradient(90deg,#dfeef0 0%,#eef6f7 40%,#f6f9fa 52%,#e4e8ea 60%,#d8dcdf 100%)}
.banner-photo{position:absolute;left:553px;top:0;width:449px;height:304px;background:linear-gradient(180deg,#e9edf0 0%,#d6dade 55%,#c9cdd1 100%)}
.banner h1{position:absolute;left:0;top:16px;width:380px;text-align:center;font-family:'Gelasio',serif;font-weight:400;font-size:29px;line-height:36px;color:var(--teal)}
.excellence{position:absolute;left:35px;top:141px;list-style:none}
.excellence li{font-family:'Dosis',sans-serif;font-weight:600;font-size:20px;color:var(--teal);height:32.5px;display:flex;align-items:center;gap:8px}
.slide-arrow{top:237px}
.welcome{left:108px;top:476px;font-family:'Oswald',sans-serif;font-weight:300;font-size:31px;line-height:40px;color:var(--orange)}
.about{left:108px;top:521px;width:617px;font-size:14px;line-height:24px;text-align:justify;color:#555}
.about p+p{margin-top:24px}
.quick{left:776px;top:475px;width:325px;height:340px}
.quick-tab{left:815px;top:474px;width:243px;height:61px;background:linear-gradient(var(--orange-light),var(--orange));display:flex;align-items:center;justify-content:center;font-family:'Alfa Slab One',serif;font-size:22px;color:#fff;letter-spacing:1px;box-shadow:0 2px 3px rgba(0,0,0,.2)}
.field{left:810px;width:258px;height:35px;background:linear-gradient(#fafafa,#e6e6e6);border:1px solid #d6d6d6;font-size:14px;color:#777;padding:9px 12px;letter-spacing:.5px}
.submit{left:990px;top:774px;width:78px;height:29px;background:var(--orange);color:#fff;font-family:'Arimo',sans-serif;font-weight:700;font-size:12px;letter-spacing:1.5px;display:flex;align-items:center;justify-content:center}
.customers{left:108px;top:853px;width:990px;height:110px;border:1px solid var(--line)}
.customers-title{left:127px;top:836px;padding:0 9px;background:#fff;font-family:'Arimo',sans-serif;font-weight:700;font-size:20px;color:var(--orange)}
.client{top:878px;height:63px;display:flex;align-items:center;justify-content:center;gap:8px;font-family:'Arimo',sans-serif;font-weight:700;font-size:19px;color:#2a3b4c}
.client i{width:12px;height:12px;background:currentColor;display:block}
.footer{left:0;top:991px;width:1200px;height:145px;background:linear-gradient(#0e7c68,#0a6655)}
.footer-bottom{left:0;top:1136px;width:1200px;height:37px;background:var(--teal);color:#fff;font-size:11px;font-weight:700;text-align:center;line-height:34px}
.links-title{left:108px;top:1001px;color:#fff;font-size:12px;font-weight:700}
.links{list-style:none;color:#fff;font-size:11px;line-height:18px}
.links li::before{content:"";display:inline-block;border-left:4px solid #fff;border-top:2.5px solid transparent;border-bottom:2.5px solid transparent;margin-right:6px;vertical-align:1px}
.address{right:108px;top:1004px;text-align:right;color:#fff;font-size:11px;line-height:18px;font-style:normal}
.address strong{font-size:12px}
</style>
</head>
<body>
<div class="abs top-strip"></div>

<div class="abs brand"><span class="brand-mark"></span>RDV Harbourline Limited</div>

<div class="abs phone">
  <svg width="28" height="24" viewBox="0 0 28 24"><ellipse cx="13" cy="14" rx="13" ry="9" fill="#0d7a66"/><path d="M8 10c1 4 4 7 8 7l2-2-3-2-1 1c-1-1-2-2-3-4l1-1-2-3z" fill="#fff"/></svg>
  <span>(852) 3000 4812</span>
</div>

<nav class="abs nav">
  <a style="left:44px">HOME</a>
  <a style="left:160px">PRODUCTS</a>
  <a style="left:314px">SERVICES</a>
  <a style="left:453px">TECHNICAL CAPABILITIES</a>
  <a style="left:721px">CONTACT US</a>
  <div class="login">
    <svg width="18" height="22" viewBox="0 0 18 22"><path d="M4 10V6a5 5 0 0 1 10 0v4" stroke="#fff" stroke-width="2.5" fill="none"/><rect x="1" y="10" width="16" height="12" rx="2" fill="#fff"/></svg>login
  </div>
</nav>

<section class="abs banner">
  <div class="banner-photo" role="img" aria-label="Photo of a business team in white shirts, one man in front with hand at his chin"></div>
  <h1>Our Printed Circuit Board<br>business is committed<br>&nbsp;to "Excellence”</h1>
  <ul class="excellence">
    <li><svg width="28" height="20" viewBox="0 0 28 20"><path d="M1 11l8 7L27 2" stroke="#0d7a66" stroke-width="3.5" fill="none"/></svg>EXCELLENCE IN QUALITY</li>
    <li><svg width="28" height="20" viewBox="0 0 28 20"><path d="M1 11l8 7L27 2" stroke="#0d7a66" stroke-width="3.5" fill="none"/></svg>EXCELLENCE IN PRICES</li>
    <li><svg width="28" height="20" viewBox="0 0 28 20"><path d="M1 11l8 7L27 2" stroke="#0d7a66" stroke-width="3.5" fill="none"/></svg>EXCELLENCE IN SERVICES</li>
    <li><svg width="28" height="20" viewBox="0 0 28 20"><path d="M1 11l8 7L27 2" stroke="#0d7a66" stroke-width="3.5" fill="none"/></svg>EXCELLENCE IN ON TIME DELIVERY</li>
  </ul>
</section>
<svg class="abs slide-arrow" style="left:62px" width="32" height="88" viewBox="0 0 32 88"><path d="M30 0 L4 44 L30 88" stroke="#0d7a66" stroke-width="6" fill="none"/></svg>
<svg class="abs slide-arrow" style="left:1105px" width="32" height="88" viewBox="0 0 32 88"><path d="M2 0 L28 44 L2 88" stroke="#0d7a66" stroke-width="6" fill="none"/></svg>

<h2 class="abs welcome">WELCOME TO RDV Harbourline Limited (RDV)</h2>
<div class="abs about">
  <p>RDV Harbourline Limited (RDV) was set up in Hong Kong in 2007 by two Hong Kong entrepreneurs, Mr. Tak Wong and Mr. Lok Fai. &nbsp;We acquired the single sided printed circuit board factory located in Dongguan City, Guangdong Province, China, from Tovand Corporation of the U.S. in 2007. In addition to RDV, Mr. Wong and Mr. Fai also own Halberd Technology Company Limited, a semiconductor company based in Hong Kong since 1997 with a total investment of over US$100 million. &nbsp;Halberd is engaged in the manufacturing of flexible substrates and the assembly of Micro Electro Mechanical Systems (MEMS).</p>
  <p>RDV has been awarded TS16949 and ISO140001 since 2005 and 2004 respectively.</p>
</div>

<svg class="abs quick" viewBox="0 0 325 340"><path d="M18 2H307L322 16V320L307 338H18L3 320V16Z" fill="#ececec" stroke="#fff" stroke-width="4"/><path d="M18 2H307L322 16V320L307 338H18L3 320V16Z" fill="none" stroke="#dcdcdc" stroke-width="1" transform="translate(0 1)"/></svg>
<div class="abs quick-tab">QUICK CONTACT</div>
<div class="abs field" style="top:543px">Name:</div>
<div class="abs field" style="top:583px">Email:</div>
<div class="abs field" style="top:623px">Company Name:</div>
<div class="abs field" style="top:664px;height:101px">Comments:</div>
<div class="abs submit">SUBMIT</div>

<div class="abs customers"></div>
<div class="abs customers-title">OUR CUSTOMERS</div>
<svg class="abs" style="left:82px;top:893px" width="18" height="22" viewBox="0 0 18 22"><path d="M15 2L4 11l11 9" stroke="#aaa" stroke-width="4" fill="none"/></svg>
<svg class="abs" style="left:1104px;top:893px" width="18" height="22" viewBox="0 0 18 22"><path d="M3 2l11 9-11 9" stroke="#aaa" stroke-width="4" fill="none"/></svg>
<div class="abs client" style="left:140px;width:120px;color:#e88a1f"><i></i>Velstone</div>
<div class="abs client" style="left:295px;width:145px;font-size:16px;color:#1f3e73">Amerton Power</div>
<div class="abs client" style="left:480px;width:222px;color:#1f6aa6"><i></i>Nexcora Energy</div>
<div class="abs client" style="left:742px;width:120px;color:#153a74">Kazumi</div>
<div class="abs client" style="left:900px;width:154px;font-size:26px;color:#16302a">Shinora</div>

<footer class="abs footer"></footer>
<div class="abs links-title">POPULAR LINKS</div>
<ul class="abs links" style="left:108px;top:1031px">
  <li>Sitemap</li><li>Circuit Boardas</li><li>Capabilities</li><li>Industries Served</li><li>About Us</li>
</ul>
<ul class="abs links" style="left:274px;top:1031px">
  <li>Contact Us</li><li>Resources</li><li>Service Center</li><li>News &amp; Events</li><li>Privacy Policy</li>
</ul>
<address class="abs address">
  <strong>RDV Harbourline Limited</strong><br>
  28/F Tidewater Plaza<br>
  17 Kestrel Road<br>
  Wan Chai, HONG KONG<br>
  Telephone: (852)30004812<br>
  Fax: (852)30004813<br>
  Email: sales@rdvboard.example
</address>
<div class="abs footer-bottom">COPYRIGHT © 2012 RDV HARBOURLINE LIMITED. ALL RIGHTS RESERVED</div>
</body>
</html>
```